Brisk Rainshield - Logo and Advert

Help to provide logo and advert.
Advert is to be short and concise to fit in a printed directory posted around homes.
Ideally the same advert to be able to be blown up as a leaflet.
Use of eco friendly type colours, soft greens and blues.
Logo to be subtle but indicative to roofing and facades.
Breakdown of advert as follows;
Company name:
Brisk Rainshield
Sub title:
Roofing & Façades
Services breakdown:
Pitched (Slating & Tiling)
Flat (Single Ply, Liquid & Mineral Felt)
Hard Metal (Zinc Standing Seam)
Leadwork
Roof lights and lanterns
Generic notes:
100% flame free applications available, eliminating all fire risks to your property. (No gas torch’s etc.).
Expert consultation and advice.
Product warranty and/or insurance backed warranty available.
Fully insured contractor.
Contact information:
Phone number to be confirmed
Email and/or website to be confirmed.
Please feel free to try out different colours and fonts other than outlined. I am not limited to those and open to suggestions.
Target Market(s)
Domestic/Private Home Owners/Small Buidlers
Industry/Entity Type
Roofing
Font styles to use
Look and feel
Each slider illustrates characteristics of the customer's brand and the style your logo design should communicate.

```html
<!DOCTYPE html>
<html lang="en">
<head>
<meta charset="utf-8">
<title>Brisk Rainshield – Roofing &amp; Façades</title>
<link href="https://fonts.googleapis.com/css2?family=Libre+Baskerville:wght@400&family=Cinzel:wght@600&family=Poppins:wght@400&family=Roboto+Condensed:wght@400&display=swap" rel="stylesheet">
<style>
  :root {
    --ink: #000000;
    --deep-blue: #0f2a6b;
    --bright-blue: #3a6cc4;
    --navy-shade: #0b1a33;
    --leaf: #7ed321;
    --label-green: #76d11e;
    --paper: #ffffff;
  }
  * { margin: 0; padding: 0; box-sizing: border-box; }
  html, body { width: 933px; height: 1200px; overflow: hidden; background: var(--ink); }
  .advert {
    position: relative; width: 933px; height: 1200px; overflow: hidden;
    background: var(--ink); color: var(--paper);
    font-family: "Libre Baskerville", Georgia, serif;
  }
  .hex-layer { position: absolute; inset: 0; }
  .abs { position: absolute; }
  .tagline {
    left: 344px; width: 320px; top: 38px; text-align: center;
    font-size: 24px; line-height: 36px; white-space: nowrap;
  }
  .wordmark { color: var(--paper); font-weight: 400; text-align: center; white-space: nowrap; }
  .wordmark .name { display: block; }
  .wordmark .sub { display: block; }
  .wordmark-top { left: 21px; top: 100px; width: 304px; }
  .wordmark-top .name { font-size: 26px; }
  .wordmark-top .sub { font-size: 14px; margin-top: 8px; letter-spacing: 1px; }
  .wordmark-faint { left: 677px; top: 604px; width: 224px; opacity: 0.18; }
  .wordmark-faint .name { font-size: 15px; }
  .wordmark-faint .sub { font-size: 9px; margin-top: 4px; letter-spacing: 0.5px; }
  .wordmark-foot { left: 400px; top: 1064px; width: 240px; }
  .wordmark-foot .name { font-size: 18px; }
  .wordmark-foot .sub { font-size: 10px; margin-top: 4px; letter-spacing: 0.8px; }
  .photo-label {
    background: var(--label-green); color: #0d1a05; height: 25px; width: 96px;
    font-family: "Roboto Condensed", Arial, sans-serif; font-size: 13px;
    line-height: 25px; text-align: center; white-space: nowrap;
  }
  .section-title {
    font-family: "Cinzel", Georgia, serif; font-weight: 600; color: var(--leaf);
    font-size: 24px; letter-spacing: 0.5px; white-space: nowrap;
  }
  .why-title { right: 35px; top: 772px; }
  .why-list { right: 35px; top: 820px; width: 470px; list-style: none; text-align: right; font-size: 14.5px; line-height: 25px; }
  .why-list li { margin-bottom: 10px; }
  .why-list .tick { display: inline-block; width: 14px; height: 14px; vertical-align: -2px; margin-left: 4px; }
  .services-title { left: 21px; top: 983px; }
  .services-list { left: 23px; top: 1026px; list-style: none; font-size: 15px; line-height: 29.5px; white-space: nowrap; }
  .services-list li::before { content: "•"; margin-right: 8px; }
  .contact { font-family: "Poppins", Arial, sans-serif; font-size: 13px; line-height: 20px; white-space: nowrap; }
  .address { left: 448px; top: 1130px; }
  .phone { right: 79px; top: 1100px; text-align: right; font-size: 14px; }
  .email { right: 79px; top: 1150px; text-align: right; }
</style>
</head>
<body>
<main class="advert">
  <svg class="hex-layer" width="933" height="1200" viewBox="0 0 933 1200" xmlns="http://www.w3.org/2000/svg">
    <defs>
      <linearGradient id="blueHex" x1="0" y1="0" x2="0" y2="1">
        <stop offset="0" stop-color="#3a6cc4"/><stop offset="1" stop-color="#0f2a6b"/>
      </linearGradient>
      <linearGradient id="servicesHex" x1="0" y1="0" x2="0" y2="1">
        <stop offset="0" stop-color="#3a6cc4"/><stop offset="1" stop-color="#0d2766"/>
      </linearGradient>
      <linearGradient id="zincFill" x1="0" y1="0" x2="1" y2="1">
        <stop offset="0" stop-color="#a9acaf"/><stop offset="1" stop-color="#8a8d90"/>
      </linearGradient>
      <linearGradient id="leadFill" x1="0" y1="0" x2="1" y2="1">
        <stop offset="0" stop-color="#8f9596"/><stop offset="0.55" stop-color="#5b6163"/><stop offset="1" stop-color="#b9c0b6"/>
      </linearGradient>
      <linearGradient id="membraneFill" x1="0" y1="0" x2="1" y2="1">
        <stop offset="0" stop-color="#dfe9f3"/><stop offset="0.45" stop-color="#8eaed6"/><stop offset="1" stop-color="#4c7ab4"/>
      </linearGradient>
      <linearGradient id="lanternFill" x1="0" y1="0" x2="0" y2="1">
        <stop offset="0" stop-color="#5a8fcf"/><stop offset="0.55" stop-color="#7f93a6"/><stop offset="1" stop-color="#6a6e71"/>
      </linearGradient>
      <linearGradient id="pitchedFill" x1="0" y1="0" x2="0" y2="1">
        <stop offset="0" stop-color="#7c8183"/><stop offset="0.6" stop-color="#8a8c8d"/><stop offset="1" stop-color="#8a5446"/>
      </linearGradient>
    </defs>

    <polygon points="-12,199.5 143,279 143,437 -12,516.5" fill="var(--navy-shade)"/>
    <polygon points="504,-74.5 659,5 659,163 504,242.5 349,163 349,5" fill="url(#blueHex)"/>

    <polygon points="855,-79 1020,6 1020,176 855,261 690,176 690,6" fill="none" stroke="#1d3f9a" stroke-width="3"/>
    <polygon role="img" aria-label="Photo: zinc standing seam roof panels" points="855,-67.5 1010,12 1010,170 855,249.5 700,170 700,12" fill="url(#zincFill)"/>

    <polygon role="img" aria-label="Photo: close-up of lead flashing work" points="333,197.5 488,277 488,435 333,514.5 178,435 178,277" fill="url(#leadFill)"/>
    <polygon role="img" aria-label="Photo: roll of waterproof membrane with water droplets" points="679,197.5 834,277 834,435 679,514.5 524,435 524,277" fill="url(#membraneFill)"/>

    <polygon points="155,456.5 328,556 328,754 155,853.5 -18,754 -18,556" fill="none" stroke="#1d3f9a" stroke-width="3"/>
    <polygon role="img" aria-label="Photo: glazed roof lantern under blue sky" points="155,466.5 320,561 320,749 155,843.5 -10,749 -10,561" fill="url(#lanternFill)"/>

    <polygon role="img" aria-label="Photo: tiled pitched roof on a brick house" points="503,467.5 658,547 658,705 503,784.5 348,705 348,547" fill="url(#pitchedFill)"/>

    <polygon points="789,478.5 900.5,535 900.5,649 789,705.5 677.5,649 677.5,535" fill="#0c1a33"/>
    <polygon points="394,743.5 505.5,800 505.5,914 394,970.5 282.5,914 282.5,800" fill="#0b1607"/>

    <polygon points="112,839 392,1000.5 392,1323.5 112,1485 -168,1323.5 -168,1000.5" fill="url(#servicesHex)"/>

    <circle cx="425" cy="1149" r="18" fill="var(--leaf)"/>
    <path d="M425 1139 a6 6 0 0 1 6 6 c0 5 -6 12 -6 12 s-6 -7 -6 -12 a6 6 0 0 1 6 -6z" fill="none" stroke="#13310a" stroke-width="1.6"/>
    <circle cx="425" cy="1145" r="2.2" fill="none" stroke="#13310a" stroke-width="1.4"/>

    <circle cx="879" cy="1109" r="18" fill="var(--leaf)"/>
    <path d="M871 1102 l4 -2 3 5 -2.5 2 c1.5 3 3.5 5 6.5 6.5 l2 -2.5 5 3 -2 4 c-8 0 -16 -8 -16 -16z" fill="none" stroke="#13310a" stroke-width="1.5" stroke-linejoin="round"/>

    <circle cx="879" cy="1159" r="18" fill="var(--leaf)"/>
    <rect x="870" y="1153" width="18" height="13" fill="none" stroke="#13310a" stroke-width="1.5"/>
    <path d="M870 1153 l9 7 9 -7" fill="none" stroke="#13310a" stroke-width="1.5"/>
  </svg>

  <div class="abs tagline">Local Owned &amp; Operated<br>Professional Service<br>Affordable Rates</div>

  <div class="abs wordmark wordmark-top"><span class="name">Brisk Rainshield</span><span class="sub">Roofing &amp; Façades</span></div>
  <div class="abs wordmark wordmark-faint"><span class="name">Brisk Rainshield</span><span class="sub">Roofing &amp; Façades</span></div>

  <div class="abs photo-label" style="left:796px;top:185px;width:119px">Zinc Standing Seam</div>
  <div class="abs photo-label" style="left:288px;top:450px">Lead Works</div>
  <div class="abs photo-label" style="left:626px;top:450px">Membrane</div>
  <div class="abs photo-label" style="left:104px;top:516px">Roof Lantern</div>
  <div class="abs photo-label" style="left:459px;top:723px">Pitched Roof</div>

  <h2 class="abs section-title why-title">Why Choose Us</h2>
  <ul class="abs why-list">
    <li>100% Flame Free Applications Available, <svg class="tick" viewBox="0 0 14 14"><circle cx="7" cy="7" r="6" fill="none" stroke="#7ed321" stroke-width="1.6"/><path d="M4 7 l2 2 5 -5" fill="none" stroke="#7ed321" stroke-width="1.8"/></svg><br>Eliminating All Fire Risks To Your Property&nbsp;&nbsp;&nbsp;&nbsp;&nbsp;</li>
    <li>Expert Consultation And Advice <svg class="tick" viewBox="0 0 14 14"><circle cx="7" cy="7" r="6" fill="none" stroke="#7ed321" stroke-width="1.6"/><path d="M4 7 l2 2 5 -5" fill="none" stroke="#7ed321" stroke-width="1.8"/></svg></li>
    <li>Product Warranty And/or Insurance <svg class="tick" viewBox="0 0 14 14"><circle cx="7" cy="7" r="6" fill="none" stroke="#7ed321" stroke-width="1.6"/><path d="M4 7 l2 2 5 -5" fill="none" stroke="#7ed321" stroke-width="1.8"/></svg><br>Backed Warranty Available&nbsp;&nbsp;&nbsp;&nbsp;&nbsp;</li>
    <li>Fully Insured Contractor <svg class="tick" viewBox="0 0 14 14"><circle cx="7" cy="7" r="6" fill="none" stroke="#7ed321" stroke-width="1.6"/><path d="M4 7 l2 2 5 -5" fill="none" stroke="#7ed321" stroke-width="1.8"/></svg></li>
  </ul>

  <h2 class="abs section-title services-title">Our Services</h2>
  <ul class="abs services-list">
    <li>Pitched (Slating &amp; Tiling)</li>
    <li>Flat (Single Ply, Liquid &amp; Mineral Felt)</li>
    <li>Hard Metal (Zinc Standing Seam)</li>
    <li>Leadwork</li>
    <li>Roof Lights And Lanterns</li>
  </ul>

  <div class="abs wordmark wordmark-foot"><span class="name">Brisk Rainshield</span><span class="sub">Roofing &amp; Façades</span></div>

  <div class="abs contact address">Street Name, City Name<br>State Zipcode</div>
  <div class="abs contact phone">123-456-7810</div>
  <div class="abs contact email">info@briskrainshield.com</div>
</main>
</body>
</html>
```